Real Estate Webpage Design

We have an existing website: ferndaleestatecollective.com.au
We focus customised service mainly on Property Management and second-hand property sales.
We are not entirely happy about the current design and layout can stay roughly the same as the back end coding is linked to a CRM system.
We would like to see the design are more reachable to our clients and appearing.
Please check our Website Design Draft for more details.

Industry/Entity Type

Real estate Agency

Number of Pages Required

5+ page

Font styles to use
Sans Serif

Colors

Designer to choose colors to be used in the design.

```html
<!DOCTYPE html>
<html lang="en">
<head>
<meta charset="utf-8">
<title>Ferndale Estate Collective – About Us</title>
<link href="https://fonts.googleapis.com/css2?family=Poppins:wght@300;400;500;600&display=swap" rel="stylesheet">
<style>
:root{
  --gold:#e9bc5c;
  --navy:#132a45;
  --cream:#f8edd3;
  --text:#7b7b82;
  --dark:#1c2230;
  --white:#ffffff;
}
*{box-sizing:border-box;margin:0;padding:0}
html,body{width:728px;height:1200px;overflow:hidden;background:var(--white)}
body{position:relative;font-family:'Poppins',sans-serif;color:var(--dark)}
.abs{position:absolute}
/* header */
.site-header{left:0;top:0;width:728px;height:36px;background:var(--white)}
.brand-box{left:37px;top:0;width:136px;height:46px;background:var(--white);z-index:3;display:flex;align-items:center;gap:6px;padding-left:10px}
.brand-mark{display:block;flex:none;width:16px;height:16px;background:var(--gold)}
.brand-name{font-size:10.5px;font-weight:500;color:var(--gold);line-height:1.1}
.main-nav{left:264px;top:14px;display:flex;font-size:8.5px;z-index:3}
.main-nav a{color:var(--dark);text-decoration:none;margin-right:15px}
.main-nav a.active{color:var(--gold);border-bottom:1.5px solid var(--gold);padding-bottom:6px}
.btn-add{left:614px;top:11px;width:77px;height:21px;background:var(--gold);color:var(--white);font-size:8.5px;display:flex;align-items:center;justify-content:center;z-index:3;white-space:nowrap}
/* hero */
.hero{left:0;top:36px;width:728px;height:214px;background:linear-gradient(100deg,#2d3a2a 0%,#3f4a48 30%,#7e8e9c 55%,#4b6440 80%,#3b5530 100%)}
.hero-title{left:37px;top:88px;font-size:23.5px;font-weight:600;color:var(--gold);line-height:30px;z-index:2}
.hero-sub{left:37px;top:151px;font-size:8.5px;color:var(--white);font-weight:300;z-index:2}
.search{left:37px;top:174px;width:291px;height:32px;background:var(--white);z-index:2;display:flex;align-items:stretch}
.search .want{width:64px;flex:none;border-right:1px solid #e2e2e2;padding:5px 8px}
.search .loc{flex:1;min-width:0;padding:5px 5px}
.search small{display:block;font-size:6.3px;line-height:9px;color:var(--gold)}
.search span{display:block;font-size:7.5px;line-height:12px;color:var(--dark);white-space:nowrap;overflow:hidden;text-overflow:ellipsis}
.search .loc span{color:var(--text)}
.search .go{width:27px;flex:none;height:28px;margin:2px;background:var(--gold);display:flex;align-items:center;justify-content:center}
/* about */
.about{left:37px;top:233px;width:655px;height:272px;background:var(--cream);text-align:center;z-index:2}
.about h2{font-size:15.5px;font-weight:600;color:var(--navy);margin-bottom:6px;line-height:22px}
.about p{font-size:8.3px;line-height:13.6px;color:var(--text);width:396px;margin:0 auto 5px}
.h-who{padding-top:27px}
.h-what{margin-top:18px}
/* promise */
.photo-frame{left:37px;top:560px;width:249px;height:249px;background:var(--white);box-shadow:0 0 6px rgba(0,0,0,.08)}
.photo{left:43px;top:565px;width:237px;height:239px;background:linear-gradient(180deg,#8fb1d6 0%,#c9cccd 40%,#9a9995 80%,#6f9d3c 100%)}
.promise{left:328px;top:553px;width:335px}
.promise h3{font-size:15.5px;font-weight:600;color:var(--navy);line-height:22px}
.promise p{font-size:8.3px;line-height:13.6px;color:var(--text)}
.promise .lead{font-size:8.3px;font-weight:500;color:var(--navy);line-height:12px}
.promise .block{margin-bottom:22px}
/* cta */
.cta{left:0;top:861px;width:728px;height:137px;background:var(--navy);text-align:center}
.cta h2{margin-top:28px;font-size:14px;font-weight:600;color:var(--white);line-height:23px}
.cta .btn{display:inline-block;margin-top:16px;background:var(--gold);color:var(--white);font-size:8.5px;line-height:11px;padding:5px 10px;white-space:nowrap}
/* footer */
.foot-brand{left:37px;top:1023px;display:flex;align-items:center;gap:6px}
.foot-about{left:37px;top:1061px;width:130px;font-size:7.8px;line-height:13.6px;color:var(--dark)}
.foot-col h4{font-size:8.5px;font-weight:500;color:var(--gold);margin-bottom:12px}
.sitemap{left:201px;top:1021px}
.sitemap li{list-style:none;font-size:7.5px;line-height:16.2px;padding-left:1px}
.contact{left:372px;top:1021px;width:170px}
.contact .row{display:flex;gap:8px;font-size:7.5px;line-height:12px;margin-bottom:8px}
.contact svg{flex:none}
.contact b{font-weight:600}
.follow{left:539px;top:1021px}
.socials{display:flex;gap:9px}
.socials i{display:block;width:24px;height:24px;border:1px solid var(--gold);border-radius:50%}
.socials i:first-child{background:var(--gold)}
.legal{left:0;top:1177px;width:728px;border-top:1px solid #e3e3e3;height:23px;font-size:7.5px;display:flex;justify-content:space-between;align-items:center;padding:0 37px;white-space:nowrap}
.legal nav span{margin-left:13px}
</style>
</head>
<body>
<header class="abs site-header"></header>
<div class="abs brand-box"><i class="brand-mark"></i><span class="brand-name">Ferndale<br>Estate Collective</span></div>
<nav class="abs main-nav">
  <a href="#">Home</a><a href="#" class="active">About Us</a><a href="#">Leasing</a><a href="#">Buy</a><a href="#">Sell</a><a href="#">Our Team</a><a href="#">Blog</a><a href="#">Contact Us</a>
</nav>
<div class="abs btn-add">Add Properties</div>

<div class="abs hero" role="img" aria-label="Modern two-storey timber and glass house surrounded by trees"></div>
<h1 class="abs hero-title">Welcome To Ferndale<br>Estate Collective</h1>
<p class="abs hero-sub">Your local real estate property group</p>
<div class="abs search">
  <div class="want"><small>I WANT TO</small><span>Buy House</span></div>
  <div class="loc"><small>Location</small><span>Enter Street adress,city,town,zip,school district...</span></div>
  <div class="go"><svg width="13" height="13" viewBox="0 0 14 14" fill="none" stroke="#fff" stroke-width="1.4"><circle cx="6" cy="6" r="4.6"/><line x1="9.4" y1="9.4" x2="13" y2="13"/></svg></div>
</div>

<section class="abs about">
  <h2 class="h-who">Who Is Ferndale?</h2>
  <p>Home means more than a house; buying a property is one of the most expensive expenses and important assets for people. Ferndale is a real estate company located in Millbrook, Canberra.</p>
  <p>Being a portfolio sales agent and property manager, coupled with our high–profile international real estate experience, Ferndale is considered a market leader on the cutting edge with deep industry knowledge, ranging from landlord–tenant relationships, residential purchases.</p>
  <h2 class="h-what">What do we do?</h2>
  <p>Helping landlords and vendor alike to complete efficient property transactions is our signature talent. Our poise, precision, and insight give us an unparalleled advantage. Beyond the core real estate services, we engender trust and cultivate relationships, an approach that generates repeat business from a high–quality client base.</p>
</section>

<div class="abs photo-frame"></div>
<div class="abs photo" role="img" aria-label="Contemporary concrete three-storey house on a lawn"></div>
<section class="abs promise">
  <div class="block"><h3>Our Promise:</h3><p>Ferndale Estate Collective aims to at all times maintain the utmost levels of service for our customers and strives to place itself at the forefront of Property Management Services within the Real Estate industry.</p></div>
  <div class="block"><h3>Why choose us?</h3><p class="lead">We care people, we value service.</p><p>Since we connect people to their homes and to their communities. Relationships are everything to us. Our clients' needs and best interests are at the heart of everything we do.</p></div>
  <div class="block"><h3>Work with us and see the<br>potential</h3><p>We are here to guide you into your dream property and will always enjoy being part of your first step to completing that project you've always dreamed of.</p></div>
</section>

<section class="abs cta">
  <h2>Contact Us If You Want To Sell Your House Or You<br>Have Other Questions</h2>
  <span class="btn">Request Free Consultation</span>
</section>

<div class="abs foot-brand"><i class="brand-mark"></i><span class="brand-name" style="font-size:12px">Ferndale<br>Estate Collective</span></div>
<p class="abs foot-about">Lorem ipsum dolor sit amet, consectetur adipiscing elit, sed do eiusmod tempor...</p>
<div class="abs foot-col sitemap"><h4>Site Map</h4><ul><li>Home</li><li>About Us</li><li>Leasing</li><li>Buy</li><li>Sell</li><li>Our Team</li><li>Blog</li><li>Contact Us</li></ul></div>
<div class="abs foot-col contact"><h4>Contact Us</h4>
  <div class="row"><svg width="12" height="13" viewBox="0 0 12 14" fill="none" stroke="#1c2230" stroke-width=".9"><path d="M6 13S1.5 8 1.5 5a4.5 4.5 0 0 1 9 0C10.5 8 6 13 6 13z"/><circle cx="6" cy="5" r="1.6"/></svg><span>18/4 Wattlebrook Crescent,<br>Millbrook, ACT, 2990</span></div>
  <div class="row"><svg width="12" height="12" viewBox="0 0 12 12" fill="none" stroke="#1c2230" stroke-width=".9"><path d="M2 1h2.5l1 3-1.5 1a7 7 0 0 0 3 3l1-1.5 3 1V10a1 1 0 0 1-1 1C5 11 1 7 1 2a1 1 0 0 1 1-1z"/></svg><span><b>02 5550 1234</b><br><b>02 5550 5678</b></span></div>
  <div class="row"><svg width="13" height="10" viewBox="0 0 13 10" fill="none" stroke="#1c2230" stroke-width=".9"><rect x=".5" y=".5" width="12" height="9"/><path d="M.5.5l6 5 6-5"/></svg><span>hello@ferndaleestate.com</span></div>
</div>
<div class="abs foot-col follow"><h4>Follow On Us</h4><div class="socials" aria-label="Social media links"><i></i><i></i><i></i><i></i></div></div>

<footer class="abs legal"><span>2022© Ferndale Estate Properties. All right reserved.</span><nav><span>Privacy</span><span>Complaint Handling &amp; Dispute Resolution</span><span>Due Diligence Checklist</span></nav></footer>
</body>
</html>
```